Psychotherapy, Life Coaching, Writer, Motivational Speaker

I am a psychotherapist, life coach, writer and speaker on health and wellness issues. I am a humanist - who believes that we are born to self-actualize - but life - changes that course. That we develop armor and coping mechanisms that divert our growth. I help people examine their road blocks to happiness. My business is unique in that I do concierge therapy. I work intensively - with multi-day sessions, I work internationally through tele-therapy - and traditionally - in an office space. My work is tailored to your needs.

Target Market(s)

Broad

Industry/Entity Type

Health

Contact Information for Business Card

Listen And Grow
Sam Perriton
248 East 39th Street
New York, NY 10027
(305) 555-0173

Requirements
Must have
• Clean lines... not too busy...
• FB page listing: Listen And Grow
• my Web page: www.listenandgrow-example.com
Nice to have
• I would love to be able to list the services: Psychotherapist, Life Coach, Motivational Speaker and Writer - but also don't want a crazy crowded card. Feel free to use the back for description.
Should not have
• Stay away from corny imagery - lotus flowers, zen, lily pond, clouds.

```html
<!DOCTYPE html>
<html lang="en">
<head>
<meta charset="utf-8">
<title>Listen And Grow – Business Card</title>
<link href="https://fonts.googleapis.com/css2?family=Lato:wght@400;700&display=swap" rel="stylesheet">
<style>
  :root {
    --bg: #e4e4e4;
    --card: #ffffff;
    --brand-blue: #4a72b0;
    --band-blue: #3f68a8;
    --ink: #161616;
    --swoosh: #111111;
  }
  * { box-sizing: border-box; margin: 0; padding: 0; }
  html, body {
    width: 1200px; height: 720px; overflow: hidden;
    background: var(--bg);
    font-family: "Lato", Arial, sans-serif;
    color: var(--ink);
  }
  .stage { position: relative; width: 1200px; height: 720px; }
  .card {
    position: absolute; top: 241px;
    width: 420px; height: 239px;
    background: var(--card);
    border-radius: 12px;
    overflow: hidden;
  }
  .card--front { left: 148px; }
  .card--back { left: 633px; }
  .card__art { position: absolute; inset: 0; width: 420px; height: 239px; }

  .brand {
    position: absolute; left: 19px; top: 20px;
    font-size: 24px; font-weight: 700; color: var(--brand-blue);
    letter-spacing: 0.1px;
  }
  .person { position: absolute; left: 18px; top: 81px; }
  .person__name { font-size: 16px; font-weight: 700; color: var(--brand-blue); }
  .person__creds { font-size: 14px; font-weight: 400; color: var(--ink); }
  .person__role { font-size: 13.5px; margin-top: 1px; }

  .contact { position: absolute; left: 19px; top: 130px; list-style: none; }
  .contact li {
    display: flex; align-items: center; gap: 4px;
    font-size: 13.5px; line-height: 15.7px;
  }
  .contact svg { width: 10px; height: 10px; flex: none; fill: var(--band-blue); }
  .contact .square { width: 9px; height: 9px; background: var(--band-blue); border-radius: 1px; flex: none; margin-right: 1px; }

  .address {
    position: absolute; right: 12px; top: 148px;
    text-align: right; font-size: 12px; line-height: 14.5px;
  }

  .back__brand {
    position: absolute; left: 16px; top: 58px;
    font-size: 20.5px; font-weight: 700; color: var(--brand-blue);
  }
  .services {
    position: absolute; left: 16px; top: 97px;
    list-style: none; font-size: 13.5px; line-height: 16px;
  }
  .appointment {
    position: absolute; left: 18px; top: 165px;
    font-size: 13.5px; white-space: nowrap;
  }
</style>
</head>
<body>
<main class="stage">

  <section class="card card--front" aria-label="Business card front">
    <svg class="card__art" viewBox="0 0 420 239" aria-hidden="true">
      <path d="M0,199 C70,206 150,216 215,222 C150,223 70,222 0,214 Z" fill="var(--swoosh)"/>
      <path d="M0,222 C100,224 200,214 260,205 C320,196 365,197 420,221 L420,239 L0,239 Z" fill="var(--band-blue)"/>
    </svg>

    <h1 class="brand">Listen And Grow</h1>

    <div class="person">
      <p><span class="person__name">Sam Perriton,</span> <span class="person__creds">LMHC, NCC</span></p>
      <p class="person__role">Psychotherapist.</p>
    </div>

    <ul class="contact">
      <li>
        <svg viewBox="0 0 10 10"><path d="M1,3 C1,1.5 3,1 5,1 C7,1 9,1.5 9,3 L7,3.5 L7,2.6 L3,2.6 L3,3.5 Z M2.5,4.5 L7.5,4.5 L8.5,9 L1.5,9 Z"/></svg>
        (305) 555-0173
      </li>
      <li>
        <svg viewBox="0 0 10 10"><path d="M0.5,2 L9.5,2 L9.5,8.5 L0.5,8.5 Z" /><path d="M0.8,2.3 L5,5.6 L9.2,2.3" fill="none" stroke="#fff" stroke-width="0.9"/></svg>
        sperriton.global@example.com
      </li>
      <li>
        <svg viewBox="0 0 10 10"><circle cx="5" cy="5" r="4.5"/><path d="M0.5,5 H9.5 M5,0.5 V9.5 M5,0.5 C2.5,3 2.5,7 5,9.5 M5,0.5 C7.5,3 7.5,7 5,9.5" fill="none" stroke="#fff" stroke-width="0.7"/></svg>
        www.listenandgrow-example.com
      </li>
      <li><span class="square"></span>Listen And Grow</li>
    </ul>

    <address class="address" style="font-style:normal">
      248 East 39th Street<br>
      New York, NY 10027
    </address>
  </section>

  <section class="card card--back" aria-label="Business card back">
    <svg class="card__art" viewBox="0 0 420 239" aria-hidden="true">
      <path d="M377,0 C386,35 398,80 395,125 C392,170 384,205 375,239 L420,239 L420,0 Z" fill="var(--band-blue)"/>
    </svg>

    <h2 class="back__brand">Listen And Grow</h2>
    <ul class="services">
      <li>Psychotherapy,</li>
      <li>Coaching,</li>
      <li>Wellness Media</li>
    </ul>
    <p class="appointment">Your Next Appoinment is at...................... at.............. am/pm</p>
  </section>

</main>
</body>
</html>
```